New business card/stationary for a consulting company

I am looking for a clean and very professional looking business card for my consulting company as well as corresponding stationary. I am uploading our logo. I like simple and powerful for the feel. No graphics but I am open on everything else. Below is my contact information but would like the final to be in a version I can add my employees information into and print. Thank you.

Daniel Whitcombe
dan@ferncliffadvisory.com
2870 North 9th Avenue, Summit Floor, Elm Ridge, Illinois 60531
www.ferncliffadvisory.com

Industry/Entity Type

Consulting

Contact Information for Business Card

Daniel Whitcombe
dan@ferncliffadvisory.com
www.ferncliffadvisory.com

Font styles to use
Serif
Sans Serif

Requirements
Must have
• Our logo and the business card details.
Nice to have
• our website www.ferncliffadvisory.com

```html
<!DOCTYPE html>
<html lang="en">
<head>
<meta charset="utf-8">
<title>Ferncliff Advisory – Business Card</title>
<link href="https://fonts.googleapis.com/css2?family=Open+Sans:wght@300;400;600;700&display=swap" rel="stylesheet">
<style>
  :root {
    --stage: #3b3532;
    --card: #141414;
    --card-edge: #1d1d1d;
    --ink: #f4f4f4;
    --ink-soft: #9a9a9a;
    --foil: #7d7d7d;
    --rule: #cfcfcf;
  }
  * { margin: 0; padding: 0; box-sizing: border-box; }
  html, body {
    width: 1200px; height: 864px; overflow: hidden;
    background: var(--stage);
    font-family: "Open Sans", Arial, sans-serif;
  }
  .stage {
    position: relative; width: 1200px; height: 864px;
    display: flex; align-items: center; justify-content: center; gap: 50px;
  }
  .card {
    position: relative; width: 520px; height: 297px;
    background: var(--card);
    border: 1px solid var(--card-edge);
    box-shadow: 0 14px 30px rgba(0,0,0,.45);
  }
  /* Front */
  .card-front .brand {
    position: absolute; left: 0; right: 0; top: 98px;
    display: flex; flex-direction: column; align-items: center; gap: 14px;
  }
  .brand-square {
    width: 70px; height: 30px; background: var(--foil);
  }
  .card-front .brand-name {
    font-weight: 300; font-size: 26px; letter-spacing: 1px;
    color: var(--foil); text-transform: uppercase;
  }
  .card-front .site {
    position: absolute; left: 0; right: 0; top: 205px; text-align: center;
    font-weight: 300; font-size: 12px; letter-spacing: 5px; color: var(--foil);
  }
  /* Back */
  .card-back .brand {
    position: absolute; left: 190px; top: 44px;
    display: flex; flex-direction: column; align-items: center; gap: 8px;
  }
  .card-back .brand-square { width: 70px; height: 24px; background: var(--ink); }
  .card-back .brand-name {
    font-weight: 300; font-size: 20px; letter-spacing: .5px;
    color: var(--ink); text-transform: uppercase;
  }
  .holder {
    position: absolute; left: 24px; top: 150px;
    font-weight: 700; font-size: 15px; letter-spacing: -.2px;
    color: var(--ink); text-transform: uppercase;
  }
  .divider {
    position: absolute; left: 208px; top: 132px; width: 1px; height: 112px;
    background: var(--rule);
  }
  .details {
    position: absolute; left: 228px; top: 134px;
    font-size: 13px; line-height: 17px; color: var(--ink);
    list-style: none;
  }
  .details li { display: flex; align-items: center; gap: 7px; }
  .details .plain { padding-left: 0; }
  .details svg { width: 11px; height: 11px; flex: none; }
</style>
</head>
<body>
<main class="stage">
  <section class="card card-front" aria-label="Card front">
    <div class="brand">
      <span class="brand-square"></span>
      <span class="brand-name">Ferncliff Advisory</span>
    </div>
    <p class="site">www.ferncliffadvisory.com</p>
  </section>

  <section class="card card-back" aria-label="Card back">
    <div class="brand">
      <span class="brand-square"></span>
      <span class="brand-name">Ferncliff Advisory</span>
    </div>
    <p class="holder">Daniel Whitcombe</p>
    <span class="divider"></span>
    <ul class="details">
      <li class="plain">2870 North 9th Avenue</li>
      <li class="plain">Summit Floor, Elm Ridge</li>
      <li class="plain">Illinois 60531</li>
      <li>
        <svg viewBox="0 0 12 12" aria-hidden="true"><rect x="0.5" y="2" width="11" height="8" fill="var(--ink)"/><path d="M1 2.6 6 6.6 11 2.6" stroke="var(--card)" stroke-width="1.2" fill="none"/></svg>
        dan@ferncliffadvisory.com
      </li>
      <li>
        <svg viewBox="0 0 12 12" aria-hidden="true"><circle cx="6" cy="6" r="5.5" fill="var(--ink)"/><circle cx="6" cy="6" r="2" fill="var(--card)"/></svg>
        www.ferncliffadvisory.com
      </li>
    </ul>
  </section>
</main>
</body>
</html>
```